Financial & Tax Strategies

need to get a word press site with existing domains and condense existing content on existing site, make new site dynamic, need mobile too......need to take info from my quorvia website and get modern, relevant site, less verbose on first page, way more things to click and engage people. Would like it to look like this , but with my color scheme and not quite as busy looking. I like much of the content on my tabs. Want maximize by seo capabilities on their as well. The number one thing I can say is to go to my existing website and get content, logo, etc there … www.pinegatelarkgroup.com .

Target Market(s)

Those 40 -65, business owners for at least 5 years. Higher net worth.

Number of Pages Required

5+ page

Font styles to use
Sans Serif

Colors
f04a50
e4daeb
ffffff

Requirements
Must have
• seo maximized, lots of places to click on to contact us, calls to action, relevant, conservative, want it to look like this and have the function as well.....slight variation on messaging, but like the simplicity on first view. https://www.dorrickvale.com/
Nice to have
• Some area along right side where videos we do will be.
Should not have
• feel too busy, but still have lots of opportunities to engage.

```html
<!DOCTYPE html>
<html lang="en">
<head>
<meta charset="utf-8">
<title>Pinegate Lark Group — Financial &amp; Tax Strategies</title>
<link href="https://fonts.googleapis.com/css2?family=Lato:wght@400;700&display=swap" rel="stylesheet">
<style>
:root{
  --red:#e8202a;
  --ink:#2a2a2a;
  --text:#555;
  --muted:#8a8a8a;
  --line:#e2e2e2;
  --band:#ececec;
  --page:#f7f7f7;
  --white:#fff;
  --footer:#2c2c2c;
  --field:#3d3d3d;
}
*{box-sizing:border-box;margin:0;padding:0}
html,body{width:1200px;height:3636px;overflow:hidden}
body{position:relative;background:var(--page);font-family:"Lato",Arial,sans-serif;color:var(--text)}
.abs{position:absolute}
.btn{position:absolute;background:var(--red);color:var(--white);font-size:13px;font-weight:700;border-radius:19px;height:38px;line-height:38px;text-align:center}
.section-title{position:absolute;left:0;width:1200px;text-align:center;color:var(--ink);font-size:34px;font-weight:400}
/* header */
.site-header{position:absolute;left:0;top:0;width:1200px;height:102px;background:var(--white)}
.menu-icon{left:80px;top:38px;width:24px}
.menu-icon span{display:block;height:3px;background:#444;margin-bottom:5px}
.brand{left:490px;top:28px;display:flex;align-items:center;gap:12px}
.brand-mark{width:44px;height:44px;border-radius:50%;background:#9a9a9a}
.brand-name{font-size:22px;font-weight:700;color:#555;line-height:23px;width:160px}
.call{right:80px;top:34px;display:flex;gap:10px;align-items:center}
.call-badge{width:28px;height:28px;border-radius:50%;background:var(--red);display:flex;align-items:center;justify-content:center}
.call-text{font-size:13px;line-height:15px;color:#555}
.call-text b{color:var(--red)}
/* hero */
.hero{position:absolute;left:0;top:102px;width:1200px;height:536px;background:linear-gradient(120deg,#c9d3dc 0%,#8799ab 35%,#5a6b7c 65%,#aeb8c2 100%)}
.hero-box{position:absolute;left:340px;top:201px;width:520px;height:218px;background:rgba(110,110,110,.55);text-align:center;color:var(--white)}
.hero-box h1{font-size:34px;font-weight:400;margin-top:36px}
.hero-box p{font-size:13px;line-height:15px;margin:8px auto 0;width:340px}
.hero-next{right:14px;top:250px}
.dots{display:flex;gap:7px}
.dots i{width:7px;height:7px;border-radius:50%;background:#ccc;display:block}
.dots i.on{background:var(--red)}
/* about */
.divider{left:540px;top:755px;width:120px;height:16px}
.about-text{left:228px;top:790px;width:744px;text-align:center;font-size:13px;line-height:17px;color:#444}
/* services */
.service{position:absolute;top:1071px;width:242px;height:274px;background:var(--white);border-radius:14px;text-align:center;padding:0 18px}
.service.active{background:var(--red);color:var(--white)}
.service svg.icon{margin-top:34px}
.service h3{font-size:17px;font-weight:400;color:#333;line-height:20px;margin-top:10px;height:40px}
.service.active h3,.service.active p{color:var(--white)}
.service p{font-size:12.5px;line-height:15px;color:var(--muted);margin-top:14px}
.service .go{position:absolute;left:111px;bottom:22px}
/* graph band */
.graph-band{position:absolute;left:0;top:1445px;width:1200px;height:511px;background:linear-gradient(110deg,#e4e4e4,#f3f3f3 50%,#e6e6e6)}
.graph-band h2{position:absolute;left:80px;top:96px;font-size:34px;font-weight:400;color:var(--ink);line-height:40px;width:460px}
.graph-band p{position:absolute;left:80px;width:440px;font-size:13px;line-height:16px;color:var(--muted)}
.screen{position:absolute;left:540px;top:66px;width:636px;height:370px}
/* blogs */
.blog{position:absolute;top:2094px;width:345px;height:388px;background:var(--white)}
.blog .photo{margin:8px;height:213px}
.blog .meta{display:flex;justify-content:space-between;font-size:12px;color:#666;margin:10px 14px 0}
.blog h4{font-size:14px;color:#333;margin:16px 14px 0}
.blog p{font-size:13px;line-height:16px;color:#555;margin:8px 14px 0}
.blog .more{font-size:12px;color:#333;margin:12px 14px 0;border-bottom:1px solid #999;display:inline-block}
.blog .bar{position:absolute;left:145px;bottom:0;width:55px;height:3px;background:var(--red)}
/* testimonials */
.testimonial{position:absolute;top:2671px;width:300px;height:306px;background:var(--white);border-radius:16px;text-align:center}
.avatar{width:98px;height:98px;border-radius:50%;margin:24px auto 0;background:radial-gradient(circle at 50% 40%,#b9b2ab,#6f6a66)}
.testimonial h5{font-size:16px;font-weight:400;color:#333;margin-top:14px}
.testimonial .role{font-size:12px;color:var(--red);margin-top:2px}
.testimonial p{font-size:13px;line-height:16px;color:#555;margin:10px auto 0;width:200px}
.testimonial .go{position:absolute;left:140px;bottom:26px}
/* newsletter */
.news-field{left:315px;top:3162px;width:425px;height:38px;background:var(--white);border-radius:19px;font-size:12px;color:#999;line-height:38px;padding-left:24px}
/* footer */
.site-footer{position:absolute;left:0;top:3260px;width:1200px;height:328px;background:var(--footer);color:#ddd}
.site-footer h6{position:absolute;top:48px;font-size:15px;font-weight:400;color:var(--white)}
.foot-brand{left:80px;top:58px;display:flex;align-items:center;gap:10px}
.foot-brand .brand-mark{background:#d8d8d8}
.foot-brand .brand-name{color:var(--white)}
.foot-about{left:80px;top:118px;width:250px;font-size:12.5px;line-height:16px}
.foot-more{left:80px;top:225px;font-size:12.5px;border-bottom:1px solid #ddd}
.links{left:388px;top:80px;font-size:12.5px;line-height:20px;list-style:none}
.links li::before{content:"";display:inline-block;width:5px;height:5px;border-radius:50%;background:var(--red);margin-right:12px;vertical-align:middle}
.address{left:601px;top:80px;font-size:12.5px;line-height:18px;width:200px}
.address div{display:flex;gap:10px;margin-bottom:4px}
.address svg{flex:none;margin-top:2px}
.f-field{position:absolute;height:26px;background:var(--field);font-size:11px;color:#ddd;padding:6px 6px}
.copy-bar{position:absolute;left:0;top:3588px;width:1200px;height:48px;background:var(--white)}
.copy-bar span{position:absolute;left:80px;top:17px;font-size:11.5px;color:#444}
.social{position:absolute;right:80px;top:13px;display:flex;gap:8px}
.social i{width:22px;height:22px;border-radius:50%;background:var(--red);display:block}
.social i.dark{background:#444}
</style>
</head>
<body>

<header class="site-header">
  <div class="abs menu-icon"><span></span><span></span><span></span></div>
  <div class="abs brand"><div class="brand-mark"></div><div class="brand-name">Pinegate Lark Group</div></div>
  <div class="abs call">
    <div class="call-badge"><svg width="14" height="14" viewBox="0 0 24 24"><path fill="#fff" d="M6.6 10.8a15 15 0 0 0 6.6 6.6l2.2-2.2c.3-.3.7-.4 1-.2 1.1.4 2.3.6 3.6.6.6 0 1 .4 1 1V20c0 .6-.4 1-1 1A17 17 0 0 1 3 4c0-.6.4-1 1-1h3.5c.6 0 1 .4 1 1 0 1.3.2 2.5.6 3.6.1.3 0 .7-.2 1z"/></svg></div>
    <div class="call-text"><b>Call us Now</b><br>916.555.0142</div>
  </div>
</header>

<section class="hero" role="img" aria-label="Photo of advisors reviewing financial charts at a desk with a laptop">
  <div class="hero-box">
    <h1>Financial &amp; Tax Strategies</h1>
    <p>Lorem Ipsum is a simply dummytext of the printing and industry when an unknown printer took galley of type.</p>
  </div>
  <div class="btn" style="left:516px;top:340px;width:168px">Get A Quote</div>
  <svg class="abs hero-next" width="22" height="34" viewBox="0 0 22 34"><path d="M4 3l14 14L4 31" stroke="#fff" stroke-width="4" fill="none"/></svg>
  <div class="abs dots" style="left:584px;top:500px"><i class="on"></i><i></i><i></i></div>
</section>

<h2 class="section-title" style="top:706px">About us</h2>
<svg class="abs divider" viewBox="0 0 120 16"><line x1="0" y1="8" x2="44" y2="8" stroke="#e8202a" stroke-width="2"/><circle cx="60" cy="8" r="6.5" fill="none" stroke="#666" stroke-width="2"/><line x1="76" y1="8" x2="120" y2="8" stroke="#e8202a" stroke-width="2"/></svg>
<p class="abs about-text">When the market is up, all advisors are brilliant. It's when the market corrects or crashes, and it always does, that all those gains are erased. How many years did it take to go up, then fall and how long to come back from the years of this process? Avoiding these "corrections" is one key.</p>
<div class="btn" style="left:516px;top:865px;width:168px">Read More</div>

<h2 class="section-title" style="top:960px">We Provide Best Services</h2>
<p class="abs" style="left:0;top:1010px;width:1200px;text-align:center;font-size:12px;color:var(--muted)">Lorem Ipsum is simply dummy text of the printing</p>

<div class="service" style="left:80px">
  <svg class="icon" width="44" height="40" viewBox="0 0 44 40"><g fill="#e8202a"><rect x="4" y="22" width="6" height="16"/><rect x="14" y="14" width="6" height="24"/><rect x="24" y="18" width="6" height="20"/><rect x="34" y="8" width="6" height="30"/><rect x="0" y="37" width="44" height="3"/></g></svg>
  <h3>Market Crash<br>Protection</h3>
  <p>Lorem Ipsum is a simply dummy text of the printing and industry when an unknown printer took galley of type.</p>
  <svg class="go" width="20" height="20" viewBox="0 0 20 20"><circle cx="10" cy="10" r="8" fill="none" stroke="#333" stroke-width="1.6"/><path d="M6 10h7M10 7l3 3-3 3" stroke="#333" stroke-width="1.6" fill="none"/></svg>
</div>
<div class="service active" style="left:344px">
  <svg class="icon" width="44" height="40" viewBox="0 0 44 40"><g fill="none" stroke="#fff" stroke-width="3"><path d="M12 4v22h22"/><path d="M34 10v16"/><path d="M4 34c12 6 26 6 36 0"/></g></svg>
  <h3>Fees Kill Retirement<br>Planning</h3>
  <p>Lorem Ipsum is a simply dummy text of the printing and industry when an unknown printer took galley of type.</p>
  <svg class="go" width="20" height="20" viewBox="0 0 20 20"><circle cx="10" cy="10" r="8" fill="none" stroke="#fff" stroke-width="1.6"/><path d="M6 10h7M10 7l3 3-3 3" stroke="#fff" stroke-width="1.6" fill="none"/></svg>
</div>
<div class="service" style="left:611px">
  <svg class="icon" width="44" height="40" viewBox="0 0 44 40"><rect x="6" y="2" width="32" height="36" fill="none" stroke="#e8202a" stroke-width="3"/><rect x="10" y="8" width="24" height="10" fill="#e8202a"/><path d="M12 25h20M12 31h14" stroke="#e8202a" stroke-width="2.5"/></svg>
  <h3>Tax<br>Avoidance</h3>
  <p>Lorem Ipsum is a simply dummy text of the printing and industry when an unknown printer took galley of type.</p>
  <svg class="go" width="20" height="20" viewBox="0 0 20 20"><circle cx="10" cy="10" r="8" fill="none" stroke="#333" stroke-width="1.6"/><path d="M6 10h7M10 7l3 3-3 3" stroke="#333" stroke-width="1.6" fill="none"/></svg>
</div>
<div class="service" style="left:877px">
  <svg class="icon" width="44" height="40" viewBox="0 0 44 40"><circle cx="22" cy="10" r="8" fill="#e8202a"/><path d="M22 18v10" stroke="#e8202a" stroke-width="3"/><path d="M12 28h20l-3 10H15z" fill="#e8202a"/></svg>
  <h3>Baby Boomer<br>Wealth Building</h3>
  <p>Lorem Ipsum is a simply dummy text of the printing and industry when an unknown printer took galley of type.</p>
  <svg class="go" width="20" height="20" viewBox="0 0 20 20"><circle cx="10" cy="10" r="8" fill="none" stroke="#333" stroke-width="1.6"/><path d="M6 10h7M10 7l3 3-3 3" stroke="#333" stroke-width="1.6" fill="none"/></svg>
</div>

<section class="graph-band">
  <h2>Graphs can speak a thousand words</h2>
  <p style="top:212px">Graphs can speak a thousand words. Here's one people really see value in. It basically shows how a $100,000.00 investment in a so-called "diversified" portfolio mirroring the Broad Index would have performed between 2000 &amp; 2010 and how one of our products would have performed.</p>
  <p style="top:298px">Harlan Wexford's number one rule is demonstrated here......DON'T LOSE MONEY. Again, we deconstruct what has been made to be difficult back to simple. Yes....</p>
  <div class="btn" style="left:80px;top:378px;width:168px">Read More</div>
  <svg class="screen" viewBox="0 0 636 370">
    <rect x="48" y="0" width="540" height="345" rx="14" fill="#1f1f1f"/>
    <rect x="62" y="14" width="512" height="312" fill="#fff"/>
    <rect x="0" y="345" width="636" height="14" rx="4" fill="#cfcfcf"/>
    <rect x="20" y="359" width="596" height="8" rx="4" fill="#9d9d9d"/>
    <text x="318" y="32" font-size="10" font-weight="700" text-anchor="middle" fill="#222" font-family="Lato,sans-serif">Historical Comparison: Broad Index vs. Protected Growth With Floor and Cap</text>
    <g font-size="10" fill="#333" font-family="Lato,sans-serif" text-anchor="end">
      <text x="96" y="62">120.00%</text><text x="96" y="106">80.00%</text><text x="96" y="150">40.00%</text><text x="96" y="186">0%</text><text x="96" y="222">-40.00%</text><text x="96" y="258">-80.00%</text><text x="96" y="294">-120.00%</text>
    </g>
    <g stroke="#e3e3e3"><line x1="104" y1="58" x2="500" y2="58"/><line x1="104" y1="102" x2="500" y2="102"/><line x1="104" y1="146" x2="500" y2="146"/><line x1="104" y1="218" x2="500" y2="218"/><line x1="104" y1="254" x2="500" y2="254"/><line x1="104" y1="290" x2="500" y2="290"/></g>
    <line x1="104" y1="182" x2="500" y2="182" stroke="#888"/>
    <g font-size="10" fill="#333" font-family="Lato,sans-serif" text-anchor="middle">
      <text x="110" y="306">00</text><text x="148" y="306">01</text><text x="186" y="306">02</text><text x="224" y="306">03</text><text x="262" y="306">04</text><text x="300" y="306">05</text><text x="338" y="306">06</text><text x="376" y="306">07</text><text x="414" y="306">08</text><text x="452" y="306">09</text><text x="490" y="306">10</text>
    </g>
    <polyline points="110,162 148,156 186,150 224,142 262,128 300,120 338,112 376,104 414,104 452,96 490,88" fill="none" stroke="#2f6db0" stroke-width="3"/>
    <g fill="#fff" stroke="#2f6db0" stroke-width="2"><circle cx="110" cy="162" r="4"/><circle cx="148" cy="156" r="4"/><circle cx="186" cy="150" r="4"/><circle cx="224" cy="142" r="4"/><circle cx="262" cy="128" r="4"/><circle cx="300" cy="120" r="4"/><circle cx="338" cy="112" r="4"/><circle cx="376" cy="104" r="4"/><circle cx="414" cy="104" r="4"/><circle cx="452" cy="96" r="4"/><circle cx="490" cy="88" r="4"/></g>
    <polyline points="110,182 148,196 186,212 224,190 262,186 300,188 338,180 376,178 414,206 452,194 490,190" fill="none" stroke="#b0202a" stroke-width="3"/>
    <g fill="#fff" stroke="#b0202a" stroke-width="2"><circle cx="110" cy="182" r="4"/><circle cx="148" cy="196" r="4"/><circle cx="186" cy="212" r="4"/><circle cx="224" cy="190" r="4"/><circle cx="262" cy="186" r="4"/><circle cx="300" cy="188" r="4"/><circle cx="338" cy="180" r="4"/><circle cx="376" cy="178" r="4"/><circle cx="414" cy="206" r="4"/><circle cx="452" cy="194" r="4"/><circle cx="490" cy="190" r="4"/></g>
    <g font-size="9" fill="#333" font-family="Lato,sans-serif"><text x="508" y="92">Gain</text><text x="508" y="196">Loss</text></g>
    <g font-size="9.5" fill="#333" font-family="Lato,sans-serif"><circle cx="180" cy="316" r="4" fill="#b0202a"/><text x="188" y="319">Annual Change in Broad Index</text><circle cx="340" cy="316" r="4" fill="#2f6db0"/><text x="348" y="319">Annual Change With Growth Cap and Floor</text></g>
  </svg>
</section>

<h2 class="section-title" style="top:2030px">Our Blogs</h2>
<article class="blog" style="left:68px">
  <div class="photo" role="img" aria-label="Photo of a vineyard landscape at sunset" style="background:linear-gradient(180deg,#c99a5a 0%,#8a6a3c 55%,#5c5a2a 100%)"></div>
  <div class="meta"><span>▦ Mar 21 , 2019</span><span>◯ 20 ♡ 12</span></div>
  <h4>What is Lorem Ipsum?</h4>
  <p>Lorem Ipsum is simply dummy the printing and typesetting industry. Lorem Ipsum has been the in the standard dummy.</p>
  <span class="more">Continue..</span><div class="bar"></div>
</article>
<article class="blog" style="left:431px">
  <div class="photo" role="img" aria-label="Photo of hands working on a laptop and paperwork" style="background:linear-gradient(135deg,#dfe6ea,#9fb0bc 60%,#6d7f8c)"></div>
  <div class="meta"><span>▦ Mar 21 , 2019</span><span>◯ 20 ♡ 12</span></div>
  <h4>What is Lorem Ipsum?</h4>
  <p>Lorem Ipsum is simply dummy the printing and typesetting industry. Lorem Ipsum has been the in the standard dummy.</p>
  <span class="more">Continue..</span><div class="bar"></div>
</article>
<article class="blog" style="left:795px">
  <div class="photo" role="img" aria-label="Photo of hands counting banknotes" style="background:linear-gradient(135deg,#2c3438,#56605a 55%,#8c907a)"></div>
  <div class="meta"><span>▦ Mar 21 , 2019</span><span>◯ 20 ♡ 12</span></div>
  <h4>What is Lorem Ipsum?</h4>
  <p>Lorem Ipsum is simply dummy the printing and typesetting industry. Lorem Ipsum has been the in the standard dummy.</p>
  <span class="more">Continue..</span><div class="bar"></div>
</article>
<div class="btn" style="left:523px;top:2512px;width:154px">View More</div>

<h2 class="section-title" style="top:2596px">Testimonials</h2>
<div class="testimonial" style="left:119px">
  <div class="avatar" role="img" aria-label="Portrait photo of client Marcus"></div>
  <h5>Marcus</h5><div class="role">Director</div>
  <p>Lorem Ipsum is simply dummy of the printing and typesetting Lorem Ipsum industry.</p>
  <svg class="go" width="20" height="20" viewBox="0 0 20 20"><circle cx="10" cy="10" r="8" fill="none" stroke="#333" stroke-width="1.6"/><path d="M6 10h7M10 7l3 3-3 3" stroke="#333" stroke-width="1.6" fill="none"/></svg>
</div>
<div class="testimonial" style="left:451px">
  <div class="avatar" role="img" aria-label="Portrait photo of client Owen Halvorsen" style="background:radial-gradient(circle at 50% 40%,#d8dde2,#8e9aa6)"></div>
  <h5>Owen Halvorsen</h5><div class="role">Director</div>
  <p>Lorem Ipsum is simply dummy of the printing and typesetting Lorem Ipsum industry.</p>
  <svg class="go" width="20" height="20" viewBox="0 0 20 20"><circle cx="10" cy="10" r="8" fill="none" stroke="#333" stroke-width="1.6"/><path d="M6 10h7M10 7l3 3-3 3" stroke="#333" stroke-width="1.6" fill="none"/></svg>
</div>
<div class="testimonial" style="left:785px">
  <div class="avatar" role="img" aria-label="Portrait photo of client Peter Lindqvist" style="background:radial-gradient(circle at 50% 40%,#c4c0bc,#5f5d5a)"></div>
  <h5>Peter Lindqvist</h5><div class="role">Director</div>
  <p>Lorem Ipsum is simply dummy of the printing and typesetting Lorem Ipsum industry.</p>
  <svg class="go" width="20" height="20" viewBox="0 0 20 20"><circle cx="10" cy="10" r="8" fill="none" stroke="#333" stroke-width="1.6"/><path d="M6 10h7M10 7l3 3-3 3" stroke="#333" stroke-width="1.6" fill="none"/></svg>
</div>
<div class="abs dots" style="left:584px;top:3004px"><i class="on"></i><i style="background:#555"></i><i class="on"></i></div>

<h2 class="section-title" style="top:3082px;font-size:26px">Join Our Newletter</h2>
<p class="abs" style="left:0;top:3122px;width:1200px;text-align:center;font-size:12px;color:#444">Sign up for Our Newletter</p>
<div class="abs news-field">Email Here</div>
<div class="btn" style="left:747px;top:3162px;width:164px">Subscribe</div>

<footer class="site-footer">
  <div class="abs foot-brand"><div class="brand-mark"></div><div class="brand-name">Pinegate Lark Group</div></div>
  <p class="abs foot-about">Lorem Ipsum is simply dummy text of the printing and typesetting industry. Lorem Ipsum has been the industry's standard dummy text ever since the 1500s,</p>
  <span class="abs foot-more">Read More..</span>

  <h6 style="left:388px">Quick Link</h6>
  <ul class="abs links"><li>Home</li><li>About us</li><li>Services</li><li>Blogs</li><li>Testimonials</li><li>Contact us</li><li>Career</li></ul>

  <h6 style="left:601px">Address</h6>
  <div class="abs address">
    <div><svg width="12" height="14" viewBox="0 0 12 14"><path d="M6 0a5 5 0 0 1 5 5c0 4-5 9-5 9S1 9 1 5a5 5 0 0 1 5-5z" fill="#ddd"/><circle cx="6" cy="5" r="2" fill="#2c2c2c"/></svg><span>48 Harbor Lane, Suite 210, Oakland, CA 94607, USA</span></div>
    <div><svg width="12" height="12" viewBox="0 0 24 24"><path fill="#ddd" d="M6.6 10.8a15 15 0 0 0 6.6 6.6l2.2-2.2c.3-.3.7-.4 1-.2 1.1.4 2.3.6 3.6.6.6 0 1 .4 1 1V20c0 .6-.4 1-1 1A17 17 0 0 1 3 4c0-.6.4-1 1-1h3.5c.6 0 1 .4 1 1 0 1.3.2 2.5.6 3.6.1.3 0 .7-.2 1z"/></svg><span>916.555.0142</span></div>
    <div><svg width="12" height="12" viewBox="0 0 12 12"><circle cx="6" cy="6" r="5" fill="none" stroke="#ddd" stroke-width="1.5"/></svg><span>916.555.0142</span></div>
    <div><svg width="12" height="12" viewBox="0 0 12 12"><rect x="1" y="2" width="10" height="8" fill="none" stroke="#ddd" stroke-width="1.4"/><path d="M1 2l5 4 5-4" fill="none" stroke="#ddd" stroke-width="1.4"/></svg><span>info@pinegatelark.com</span></div>
  </div>

  <h6 style="left:824px">Contact us</h6>
  <div class="f-field" style="left:824px;top:82px;width:92px">Name</div>
  <div class="f-field" style="left:920px;top:82px;width:92px">Email</div>
  <div class="f-field" style="left:1016px;top:82px;width:101px">Phone</div>
  <div class="f-field" style="left:824px;top:114px;width:293px;height:68px"></div>
  <div class="btn" style="left:826px;top:200px;width:140px;height:32px;line-height:32px">Subscribe</div>
</footer>

<div class="copy-bar">
  <span>CopyRight © 2019 Pinegate Lark Group. All Right Reserve</span>
  <div class="social"><i></i><i class="dark"></i><i class="dark"></i><i class="dark"></i><i class="dark"></i></div>
</div>

</body>
</html>
```